NORU-KIT vegan protein

Hi
We need a vegan protein label and logo for our company
NORU-KIT
We made a quick sketch in the type of way we want it But you can always make it better
Dont mind the logo we sketched please come up with something else
Left side of the label please the color of the taste So brown red vanille we need 3 designs for Chocolate, strawberry and vanilla
Backside: leave nutrition faces blank,
One square text with: Pea Protein derived and extracted from organic grean split peas. It is a great source of fiber (helps with digestion and less bloating), vitamines and minerals. Studies have shown that the intake of pea protein can reduce high blood pressure and that it can be used for prevention and controll of diabetes as it has minimal effect on blood glucose levels and insulin response.
One square with suggested use:
Add 1 or 2 scoops to a blender, shaker or glass with cold water or your favorite beverage (various amount of liquid to achieve your desired taste). Shake or mix well before consumption.
Distributed by:
MARBOW COMPANY BV
THE NETHERLANDS
Please make it look amazing elegant and premium elite looking
It will be made on a alu bag like a send In the pictures
Look and feel
Each slider illustrates characteristics of the customer's brand and the style your logo design should communicate.

```html
<!DOCTYPE html>
<html lang="en">
<head>
<meta charset="utf-8">
<title>NORU-KIT Organic Vegan Protein – Labels</title>
<link href="https://fonts.googleapis.com/css2?family=Montserrat:wght@700;800;900&family=Barlow+Condensed:wght@500&display=swap" rel="stylesheet">
<style>
  :root {
    --stage: #4a4b4f;
    --label-white: #f4f4f4;
    --ink: #1f1f1f;
    --badge-dark: #8a8a8a;
    --badge-light: #a9a9a9;
    --choc: #5a341a;
    --straw: #d7192a;
    --vanilla: #e6dcae;
    --vanilla-mark: #e6dcae;
  }
  * { box-sizing: border-box; margin: 0; padding: 0; }
  html, body { width: 1200px; height: 700px; overflow: hidden; }
  body {
    background: var(--stage);
    font-family: "Montserrat", Arial, sans-serif;
    display: flex;
    align-items: center;
    justify-content: center;
    gap: 28px;
  }
  .label {
    font-size: 9.6px;
    width: 34em;
    height: 48em;
    background: var(--label-white);
    display: flex;
    overflow: hidden;
  }
  .label--featured { font-size: 11.6px; }
  .label--chocolate { --band: var(--choc); --band-ink: #fff; --accent: var(--choc); --mark: var(--choc); --pill-ink: #fff; }
  .label--strawberry { --band: var(--straw); --band-ink: #fff; --accent: var(--straw); --mark: var(--straw); --pill-ink: #fff; }
  .label--vanilla { --band: var(--vanilla); --band-ink: var(--ink); --accent: #3a3a3a; --mark: var(--vanilla-mark); --pill-ink: var(--ink); }

  .brand-band {
    width: 8em;
    flex-shrink: 0;
    background: var(--band);
    display: flex;
    flex-direction: column;
    align-items: center;
    justify-content: flex-end;
    gap: 1.6em;
    padding-bottom: 2em;
  }
  .brand-name {
    writing-mode: vertical-rl;
    transform: rotate(180deg);
    white-space: nowrap;
    font-weight: 900;
    font-size: 4.2em;
    line-height: 1;
    letter-spacing: 0.01em;
    color: var(--band-ink);
  }
  .brand-name sup { font-size: 0.3em; font-weight: 700; }
  .flavour-swatch {
    width: 6.4em;
    height: 6.4em;
    flex-shrink: 0;
    border-radius: 50%;
    border: 0.3em solid #fff;
  }
  .label--chocolate .flavour-swatch { background: radial-gradient(circle, #7a4a2a, #3e2210); }
  .label--strawberry .flavour-swatch { background: radial-gradient(circle, #e24a4a 30%, #5f8f3a); }
  .label--vanilla .flavour-swatch { background: radial-gradient(circle, #fbf6e2 35%, #5a3a20); }

  .label-body {
    flex: 1;
    min-width: 0;
    display: flex;
    flex-direction: column;
    align-items: center;
    padding-top: 7.5em;
  }
  .product-title { text-align: center; color: var(--accent); line-height: 1; white-space: nowrap; }
  .product-title .line-1 { font-weight: 900; font-size: 3.2em; }
  .product-title .line-2 { font-weight: 800; font-size: 1.7em; margin-top: 0.2em; }

  .brand-mark {
    margin-top: 1.6em;
    width: 21em;
    height: 9em;
    display: flex;
    align-items: center;
    justify-content: center;
    gap: 0.8em;
  }
  .brand-mark .mark-square { width: 1.8em; height: 1.8em; background: var(--mark); flex-shrink: 0; }
  .brand-mark .mark-name { font-weight: 900; font-size: 2.6em; color: var(--mark); white-space: nowrap; }

  .claim { text-align: center; color: var(--ink); line-height: 1; margin-top: 1em; white-space: nowrap; }
  .claim .percent { font-weight: 900; font-size: 5.3em; }
  .claim .plant { font-weight: 800; font-size: 2.1em; margin-top: 0.1em; }

  .badges { display: flex; margin-top: 1.6em; }
  .badge {
    width: 4.6em; height: 4.6em; border-radius: 50%;
    background: var(--badge-dark);
    color: #fff;
    font-family: "Barlow Condensed", "Arial Narrow", sans-serif;
    font-weight: 500;
    display: flex; flex-direction: column; align-items: center; justify-content: center;
    text-align: center; line-height: 1;
  }
  .badge + .badge { margin-left: -0.2em; }
  .badge:nth-child(even) { background: var(--badge-light); margin-top: 0.9em; }
  .badge .big { font-size: 1.35em; }
  .badge .small { font-size: 0.75em; margin-top: 0.15em; }

  .net-weight {
    margin-top: 1.6em;
    background: var(--band);
    color: var(--pill-ink);
    font-weight: 700;
    font-size: 1.25em;
    padding: 0.35em 2em;
    border-radius: 1.2em 0 1.2em 0;
    white-space: nowrap;
  }
</style>
</head>
<body>

<section class="label label--chocolate" aria-label="Chocolate flavour label">
  <div class="brand-band">
    <div class="brand-name">NORU-KIT<sup>®</sup></div>
    <div class="flavour-swatch" role="img" aria-label="Chocolate pieces"></div>
  </div>
  <div class="label-body">
    <h2 class="product-title"><div class="line-1">ORGANIC</div><div class="line-2">VEGAN PROTEIN</div></h2>
    <div class="brand-mark"><span class="mark-square"></span><span class="mark-name">NORU-KIT</span></div>
    <div class="claim"><div class="percent">100%</div><div class="plant">PLANT BASED</div></div>
    <div class="badges">
      <div class="badge"><span class="big">0</span><span class="small">SUGARE</span></div>
      <div class="badge"><span class="big">7g</span><span class="small">ORGANIC</span></div>
      <div class="badge"><span class="big">21 g</span><span class="small">PROTEIN</span></div>
      <div class="badge"><span class="big">GF</span></div>
      <div class="badge"><span class="small">SUPER<br>FOOD<br>VITAMINES</span></div>
    </div>
    <div class="net-weight">Net Wt. 700 g</div>
  </div>
</section>

<section class="label label--featured label--strawberry" aria-label="Strawberry flavour label">
  <div class="brand-band">
    <div class="brand-name">NORU-KIT<sup>®</sup></div>
    <div class="flavour-swatch" role="img" aria-label="Fresh strawberries with leaves"></div>
  </div>
  <div class="label-body">
    <h2 class="product-title"><div class="line-1">ORGANIC</div><div class="line-2">VEGAN PROTEIN</div></h2>
    <div class="brand-mark"><span class="mark-square"></span><span class="mark-name">NORU-KIT</span></div>
    <div class="claim"><div class="percent">100%</div><div class="plant">PLANT BASED</div></div>
    <div class="badges">
      <div class="badge"><span class="big">0</span><span class="small">SUGARE</span></div>
      <div class="badge"><span class="big">7g</span><span class="small">ORGANIC</span></div>
      <div class="badge"><span class="big">21 g</span><span class="small">PROTEIN</span></div>
      <div class="badge"><span class="big">GF</span></div>
      <div class="badge"><span class="small">SUPER<br>FOOD<br>VITAMINES</span></div>
    </div>
    <div class="net-weight">Net Wt. 700 g</div>
  </div>
</section>

<section class="label label--vanilla" aria-label="Vanilla flavour label">
  <div class="brand-band">
    <div class="brand-name">NORU-KIT<sup>®</sup></div>
    <div class="flavour-swatch" role="img" aria-label="Vanilla flower and pods"></div>
  </div>
  <div class="label-body">
    <h2 class="product-title"><div class="line-1">ORGANIC</div><div class="line-2">VEGAN PROTEIN</div></h2>
    <div class="brand-mark"><span class="mark-square"></span><span class="mark-name">NORU-KIT</span></div>
    <div class="claim"><div class="percent">100%</div><div class="plant">PLANT BASED</div></div>
    <div class="badges">
      <div class="badge"><span class="big">0</span><span class="small">SUGARE</span></div>
      <div class="badge"><span class="big">7g</span><span class="small">ORGANIC</span></div>
      <div class="badge"><span class="big">21 g</span><span class="small">PROTEIN</span></div>
      <div class="badge"><span class="big">GF</span></div>
      <div class="badge"><span class="small">SUPER<br>FOOD<br>VITAMINES</span></div>
    </div>
    <div class="net-weight">Net Wt. 700 g</div>
  </div>
</section>

</body>
</html>
```